New business card for a regional office of a US M&A company

We need business card for a finance company, office based in Hong Kong , our Head office is in US, our business is to Merge and acquires companies , the new office will be a regional office for the Asia Pacific region. We want to use the head office logo as attached ( but don't have to be exactly the same, can be a variation to it) as a base and then add Asia Pacific alongside the logo.
We would prefer to have be bilingual Eng + Chinese, although we don't really have Chinese company name .

Industry/Entity Type

Business

Contact Information for Business Card

Clara Jo Tsang
 

VP,
APAC M&A Operations
Orin Vantage Asia Pacific Limited
 
Unit 1407, K18
18 Tai Lok Shan Road, 
Hong Kong 
 
M: +852 6038 1742
T : +852 2836 4100
F : +852 2836 4177
VOIP: 4158
 
cjtsang@orinvantage.com

Font styles to use
Serif
Sans Serif

Colors

Designer to choose colors to be used in the design.

Requirements
Must have
• APAC Office

```html
<!DOCTYPE html>
<html lang="en">
<head>
<meta charset="UTF-8">
<title>Orin Vantage Asia Pacific – Business Card</title>
<link rel="stylesheet" href="https://fonts.googleapis.com/css2?family=Noto+Sans:wght@400;700&display=swap">
<style>
  :root {
    --backdrop: #3a3a3c;
    --card: #1f2022;
    --emboss: #3d3e41;
    --emboss-light: #5a5b5f;
    --text: #f2f2f2;
    --accent: #1fa9d6;
  }
  * { box-sizing: border-box; margin: 0; padding: 0; }
  html, body {
    width: 799px; height: 1200px; overflow: hidden;
    background: var(--backdrop);
    font-family: "Noto Sans", sans-serif;
  }
  .sheet {
    width: 799px; height: 1200px;
    display: flex; flex-direction: column;
    align-items: center; justify-content: center; gap: 90px;
  }
  .card {
    position: relative;
    width: 640px; height: 366px;
    background: var(--card);
    box-shadow: 0 14px 30px rgba(0,0,0,0.45);
    overflow: hidden;
  }
  /* Front */
  .card--front {
    display: flex; align-items: center; justify-content: center; gap: 18px;
  }
  .brand-square {
    width: 44px; height: 44px;
    background: var(--emboss-light);
  }
  .brand-name {
    font-weight: 700; font-size: 46px; letter-spacing: 1px;
    color: var(--emboss-light);
    text-transform: uppercase;
  }
  /* Back */
  .card--back { color: var(--text); }
  .identity {
    position: absolute; top: 46px; left: 0; right: 0;
    text-align: center;
  }
  .identity__name {
    font-weight: 700; font-size: 21px; color: var(--accent);
  }
  .identity__title { font-size: 14px; margin-top: 2px; }
  .identity__company {
    font-weight: 700; font-size: 19px; color: var(--accent);
    text-transform: uppercase; margin-top: 8px; letter-spacing: .3px;
  }
  .contacts {
    position: absolute; top: 170px; left: 230px;
    font-size: 14px; line-height: 20px;
  }
  .contacts__label { color: var(--accent); }
  .address {
    position: absolute; bottom: 40px; left: 0; right: 0;
    text-align: center; font-size: 14px;
  }
  .accent-band {
    position: absolute; left: 0; right: 0; bottom: 0;
    height: 12px; background: var(--accent);
  }
</style>
</head>
<body>
<main class="sheet">
  <section class="card card--front" aria-label="Card front">
    <span class="brand-square"></span>
    <span class="brand-name">Orin Vantage</span>
  </section>

  <section class="card card--back" aria-label="Card back">
    <div class="identity">
      <p class="identity__name">Clara Jo Tsang</p>
      <p class="identity__title">Vice President, APAC M&amp;A Operations</p>
      <p class="identity__company">Orin Vantage Asia Pacific Limited</p>
    </div>
    <div class="contacts">
      <p>+852 6038 1742</p>
      <p>+852 2836 4100</p>
      <p>+852 2836 4177</p>
      <p><span class="contacts__label">VOIP:</span> 4158</p>
      <p>cjtsang@orinvantage.com</p>
    </div>
    <p class="address">Unit 1407, K18 18, Tai Lok Shan Road, Hong Kong</p>
    <div class="accent-band"></div>
  </section>
</main>
</body>
</html>
```